Web Developer Needs a Business Card Design

I need a personal business card design that represents me as a web developer for potential employers. I would like the background to be a dark color on the front for contrast with my logo and name. The back will have all my information along with a smaller version of the logo. I want something with a modern look and feel, not too conservative. This will be used for potential employers and freelance work.

Industry/Entity Type

Business

Contact Information for Business Card

Front should have my logo and name. The back should have all my personal information which would include: name: Tom Varulek, phone: 570-614-3098, email: tomvarulek@quillbox.net, website url: www.tomvarulek.net, logo, web developer.

Font styles to use
Sans Serif

Requirements
Must have
• Must include my logo. The color palette base color will be the logo color.

```html
<!DOCTYPE html>
<html lang="en">
<head>
<meta charset="utf-8">
<title>Tom Varulek – Business Card</title>
<link rel="stylesheet" href="https://fonts.googleapis.com/css2?family=Arimo:wght@400;500&display=swap">
<style>
  :root {
    --page: #dcdcdc;
    --card-white: #ffffff;
    --brand-green: #218a72;
    --brand-teal: #6cc5b0;
    --ink-black: #000000;
    --text-light: #ffffff;
  }
  * { margin: 0; padding: 0; box-sizing: border-box; }
  html, body {
    width: 1189px; height: 1200px; overflow: hidden;
    background: var(--page);
    font-family: "Arimo", Arial, sans-serif;
  }
  .card {
    position: absolute;
    left: 140px;
    width: 918px;
    height: 523px;
    overflow: hidden;
  }
  .card--details { top: 45px; background: var(--card-white); }
  .card--front { top: 624px; background: var(--ink-black); }

  .card__shape { position: absolute; inset: 0; }

  .brand-mark {
    position: absolute;
    display: flex;
    align-items: center;
    gap: 14px;
    color: var(--brand-teal);
    font-weight: 500;
    letter-spacing: 1px;
  }
  .brand-mark__dot {
    border-radius: 50%;
    background: var(--brand-teal);
    flex: none;
  }
  .card--details .brand-mark {
    left: 0; right: 0; top: 108px;
    justify-content: center;
    font-size: 44px;
  }
  .card--details .brand-mark__dot { width: 30px; height: 30px; }

  .identity {
    position: absolute;
    right: 574px;
    top: 340px;
    text-align: right;
    color: var(--text-light);
  }
  .identity__name { font-size: 47px; line-height: 1; font-weight: 400; }
  .identity__role { font-size: 26px; margin-top: 8px; letter-spacing: 0.5px; }

  .divider {
    position: absolute;
    left: 413px; top: 322px;
    width: 3px; height: 192px;
    background: var(--text-light);
  }

  .contact {
    position: absolute;
    left: 482px; top: 354px;
    list-style: none;
    color: var(--text-light);
    font-size: 29px;
  }
  .contact__item {
    display: flex; align-items: center;
    height: 46px;
  }
  .contact__icon { width: 18px; height: 18px; margin-right: 11px; flex: none; }

  .card--front .brand-mark {
    left: 70px; top: 226px;
    font-size: 50px;
  }
  .card--front .brand-mark__dot { width: 34px; height: 34px; }
  .front__bar {
    position: absolute;
    left: 354px; top: 232px;
    width: 4px; height: 55px;
    background: var(--text-light);
  }
  .front__name {
    position: absolute;
    left: 393px; top: 224px;
    color: var(--text-light);
    font-size: 68px;
    font-weight: 400;
    line-height: 1;
    letter-spacing: 1px;
  }
</style>
</head>
<body>

<section class="card card--details">
  <svg class="card__shape" viewBox="0 0 918 523" preserveAspectRatio="none" aria-hidden="true">
    <path d="M0 174 Q459 400 918 174 L918 523 L0 523 Z" fill="var(--brand-green)"/>
    <path d="M30 186 Q459 400 880 196 Q459 380 30 186 Z" fill="var(--ink-black)"/>
  </svg>

  <div class="brand-mark"><span class="brand-mark__dot"></span>varulek</div>

  <div class="identity">
    <p class="identity__name">Tom Varulek</p>
    <p class="identity__role">web developer</p>
  </div>

  <div class="divider"></div>

  <ul class="contact">
    <li class="contact__item">
      <svg class="contact__icon" viewBox="0 0 18 18" aria-hidden="true">
        <rect width="18" height="18" fill="#fff"/>
        <path d="M5 4 L8 4 L8 7 L7 8 Q8 10 10 11 L11 10 L14 10 L14 13 Q8 14 5 8 Z" fill="var(--brand-green)"/>
      </svg>
      570-614-3098
    </li>
    <li class="contact__item">
      <svg class="contact__icon" viewBox="0 0 18 18" aria-hidden="true">
        <rect width="18" height="18" fill="#fff"/>
        <rect x="3" y="5" width="12" height="8" fill="none" stroke="var(--brand-green)" stroke-width="1.3"/>
        <path d="M3 5 L9 10 L15 5" fill="none" stroke="var(--brand-green)" stroke-width="1.3"/>
      </svg>
      tomvarulek@quillbox.net
    </li>
    <li class="contact__item">
      <svg class="contact__icon" viewBox="0 0 18 18" aria-hidden="true">
        <rect width="18" height="18" fill="#fff"/>
        <circle cx="9" cy="9" r="5.5" fill="none" stroke="var(--brand-green)" stroke-width="1.3"/>
        <path d="M3.5 9 H14.5 M9 3.5 Q6 9 9 14.5 Q12 9 9 3.5" fill="none" stroke="var(--brand-green)" stroke-width="1.1"/>
      </svg>
      www.tomvarulek.net
    </li>
  </ul>
</section>

<section class="card card--front">
  <div class="brand-mark"><span class="brand-mark__dot"></span>varulek</div>
  <div class="front__bar"></div>
  <p class="front__name">TOM VARULEK</p>
</section>

</body>
</html>
```